New Business Card Design Project LORVANTI-Italy

we are LORVANTI-Italy
our company in the market for 3 years we are luxury cosmetic company and its about time for a facelift :)
i will like to have elegant luxurious and unique business card
that will give the person that get it a unique, luxurious and elegant impression
I'm VERY OPEN FOR NEW IDEAS , even duo i add a few files of things that i see on line and i like them

i add my logo as well
my website is LORVANTI.COM
(if you would like to see the main style that we have)

Target Market(s)

adult that have money :)

Industry/Entity Type

Business

Contact Information for Business Card

Name - Dario Lorvanti
Position - CEO and CO Founder
address - 4817 E Halvern
telephone - 555-384-1926
email - dario@lorvanti.com
fax - 555-384-1926
website - LORVANTI.COM

Colors
000000
959595
fbee3e
ffffff

Requirements
Must have
• big logo in GOLD color
• elegant look
• impressive
Nice to have
• not must but maybe classy pattern background
• not must but maybe emblem
• maybe clear plastic business card
Should not have
• colors
• images

```html
<!DOCTYPE html>
<html lang="en">
<head>
<meta charset="utf-8">
<title>LORVANTI Italy – Business Card</title>
<link href="https://fonts.googleapis.com/css2?family=Roboto:wght@400;700&display=swap" rel="stylesheet">
<style>
  :root {
    --stage: #101010;
    --card: #000000;
    --gold: #d6ab3a;
    --white: #f2f2f2;
  }
  * { margin: 0; padding: 0; box-sizing: border-box; }
  html, body {
    width: 1200px; height: 900px; overflow: hidden;
    background: var(--stage);
    font-family: "Roboto", Arial, sans-serif;
  }
  .stage { position: relative; width: 1200px; height: 900px; }
  .card {
    position: absolute;
    width: 560px; height: 320px;
    background: var(--card);
    box-shadow: 0 18px 40px rgba(0,0,0,0.6);
  }
  .card--front { left: 60px; top: 90px; }
  .card--back  { left: 580px; top: 490px; }

  .brand {
    position: absolute;
    display: flex; flex-direction: column; align-items: center;
    color: var(--gold); font-weight: 400; text-transform: uppercase;
  }
  .brand__disc { border: 2px solid var(--gold); border-radius: 50%; }
  .brand__name { letter-spacing: 0.08em; }
  .brand__place { letter-spacing: 0.2em; }

  .card--front .brand { left: 0; right: 0; top: 62px; }
  .card--front .brand__disc { width: 84px; height: 84px; margin-bottom: 18px; }
  .card--front .brand__name { font-size: 46px; line-height: 1; }
  .card--front .brand__place { font-size: 14px; margin-top: 10px; }

  .card--back .brand { right: 34px; top: 28px; }
  .card--back .brand__disc { width: 46px; height: 46px; margin-bottom: 8px; }
  .card--back .brand__name { font-size: 22px; line-height: 1; }
  .card--back .brand__place { font-size: 8px; margin-top: 5px; }

  .holder { position: absolute; left: 40px; top: 178px; }
  .holder__name {
    color: var(--gold); font-weight: 700; font-size: 24px; letter-spacing: 0.04em;
  }
  .holder__role {
    color: var(--white); font-size: 10px; letter-spacing: 0.18em; margin-top: 4px;
  }
  .contact {
    position: absolute; left: 62px; top: 240px;
    list-style: none; color: var(--white);
    font-size: 10.5px; letter-spacing: 0.16em; line-height: 1.55;
  }
  .contact__label { color: var(--gold); font-weight: 700; margin-right: 6px; }
  .address {
    position: absolute; left: 330px; top: 200px;
    font-style: normal; color: var(--white);
    font-size: 10.5px; letter-spacing: 0.16em; line-height: 1.55;
  }
  .address span { display: block; }
  .address span:nth-child(2) { padding-left: 14px; }
  .address span:nth-child(3) { padding-left: 28px; }
</style>
</head>
<body>
<main class="stage">
  <section class="card card--front" aria-label="Card front">
    <div class="brand">
      <span class="brand__disc"></span>
      <span class="brand__name">Lorvanti</span>
      <span class="brand__place">Italy</span>
    </div>
  </section>

  <section class="card card--back" aria-label="Card back">
    <div class="brand">
      <span class="brand__disc"></span>
      <span class="brand__name">Lorvanti</span>
      <span class="brand__place">Italy</span>
    </div>

    <div class="holder">
      <p class="holder__name">DARIO LORVANTI</p>
      <p class="holder__role">CEO AND CO FOUNDER</p>
    </div>

    <ul class="contact">
      <li><span class="contact__label">T</span>555-384-1926</li>
      <li><span class="contact__label">F</span>555-384-1926</li>
      <li>DARIO@LORVANTI.COM</li>
      <li>WWW.LORVANTI.COM</li>
    </ul>

    <address class="address">
      <span>4817 E HALVERN</span>
      <span>MERIDALE, NEVADA</span>
      <span>89120</span>
    </address>
  </section>
</main>
</body>
</html>
```